Business Card Design

Business Card for professional consulting firm working with large financial institutions.

Target Market(s)

Executive buyers

Industry/Entity Type

Banking

Contact Information for Business Card

Mild creativity wanted. Not boring, but do elaborate artwork.

Font styles to use
Serif
Sans Serif

Colors

Designer to choose colors to be used in the design.

Requirements
Must have
• Standard business card features - company name, individual name, telephone, website, email, locations.
Nice to have
• Two colors
Should not have
• too many colors, fancy printing, cartoons.

```html
<!DOCTYPE html>
<html lang="en">
<head>
<meta charset="UTF-8">
<title>Calloway Partners — Business Card</title>
<link rel="stylesheet" href="https://fonts.googleapis.com/css2?family=Montserrat:wght@400;500;800&family=Noto+Serif:wght@400&display=swap">
<style>
  :root {
    --backdrop: #ececec;
    --paper: #ffffff;
    --ink-dark: #2b2b2b;
    --ink-text: #2a2a2a;
    --ink-soft: #555555;
    --name-light: #8a8a8a;
    --name-on-dark: #f2f2f2;
    --rule: #c9c9c9;
  }
  * { box-sizing: border-box; margin: 0; padding: 0; }
  html, body {
    width: 1200px; height: 1184px; overflow: hidden;
    background: var(--backdrop);
  }
  .sheet {
    width: 1200px; height: 1184px;
    display: flex; flex-direction: column; align-items: center; justify-content: center;
    gap: 56px;
  }
  .card {
    width: 860px; height: 492px;
    position: relative;
    box-shadow: 0 6px 22px rgba(0,0,0,0.10);
  }
  .card--front { background: var(--paper); display: flex; }
  .card--back { background: var(--ink-dark); display: flex; align-items: center; justify-content: center; }

  .company-name {
    font-family: "Noto Serif", Georgia, serif;
    font-weight: 400;
    white-space: nowrap;
    display: inline-flex; align-items: center; gap: 14px;
  }
  .company-name__mark { width: 12px; height: 12px; border-radius: 50%; flex: none; }
  .card--front .company-name { font-size: 36px; color: var(--name-light); }
  .card--front .company-name__mark { background: var(--name-light); }
  .card--back .company-name { font-size: 64px; color: var(--name-on-dark); gap: 20px; }
  .card--back .company-name__mark { width: 18px; height: 18px; background: var(--name-on-dark); }

  .brand-panel {
    width: 50%; display: flex; align-items: center; justify-content: center;
    padding-bottom: 40px;
  }
  .divider { width: 1px; background: var(--rule); margin: 150px 0 120px; }
  .contact-panel {
    flex: 1; padding: 160px 0 0 44px;
    font-family: "Montserrat", Arial, sans-serif; color: var(--ink-text);
  }
  .person__name { font-size: 30px; font-weight: 800; letter-spacing: 0.5px; }
  .person__title { font-size: 17px; font-weight: 500; color: var(--ink-soft); margin-top: 2px; }
  .address { font-size: 17px; line-height: 1.35; margin-top: 18px; }
  .contact-list { list-style: none; margin-top: 12px; font-size: 17px; }
  .contact-list li { display: flex; align-items: center; gap: 12px; line-height: 1.5; }
  .contact-list svg { width: 16px; height: 16px; flex: none; }
</style>
</head>
<body>
<main class="sheet">
  <section class="card card--front" aria-label="Business card front">
    <div class="brand-panel">
      <span class="company-name"><span class="company-name__mark"></span>Calloway Partners</span>
    </div>
    <div class="divider"></div>
    <div class="contact-panel">
      <p class="person__name">Daniel HARLOW</p>
      <p class="person__title">Managing Director</p>
      <p class="address">418 N Market Avenue 5120<br>Ridgefield Park, OH 45011</p>
      <ul class="contact-list">
        <li>
          <svg viewBox="0 0 16 16" aria-hidden="true"><path d="M4 1.5l2.2 3-1.4 1.6c.8 1.9 2.3 3.4 4.2 4.2l1.6-1.4 3 2.2-1.3 2.6C6.5 13.5 2.5 9.5 1.4 3z" fill="none" stroke="#2a2a2a" stroke-width="1.3" stroke-linejoin="round"/></svg>
          000.000.0000
        </li>
        <li>
          <svg viewBox="0 0 16 16" aria-hidden="true"><rect x="1.5" y="3.5" width="13" height="9" fill="none" stroke="#2a2a2a" stroke-width="1.3"/><path d="M1.5 3.5L8 9l6.5-5.5" fill="none" stroke="#2a2a2a" stroke-width="1.3"/></svg>
          daniel@calloway.com
        </li>
        <li>
          <svg viewBox="0 0 16 16" aria-hidden="true"><circle cx="8" cy="8" r="6.5" fill="none" stroke="#2a2a2a" stroke-width="1.3"/><ellipse cx="8" cy="8" rx="2.8" ry="6.5" fill="none" stroke="#2a2a2a" stroke-width="1.1"/><path d="M1.5 8h13M2.5 4.8h11M2.5 11.2h11" stroke="#2a2a2a" stroke-width="1"/></svg>
          www.calloway.com
        </li>
      </ul>
    </div>
  </section>

  <section class="card card--back" aria-label="Business card back">
    <span class="company-name"><span class="company-name__mark"></span>Calloway Partners</span>
  </section>
</main>
</body>
</html>
```